Professional Single Page Website Design for Tollbrook Advisory

Tollbrook Advisory is a new business consultancy specializing in providing expert services to small businesses, primarily in the brick-and-mortar retail and food service sectors. We offer a range of services including franchise development and launch, due diligence, and construction management.

Currently, we have a basic website set up at www.tollbrookadvisory.example, but we need a professional touch to enhance its design and functionality.

Project Requirements:
- Single Page Design: For now, we need a single page design that effectively showcases who we are, our services, and contact information.
- Future Expansion: The design should be flexible and scalable for future expansion to include additional pages like specific service offerings, about us, and a dedicated contact page.
- Design Aesthetic: We are looking for a modern yet professional design that aligns with our brand identity.
- Logo: We have a logo that we like, which was also sourced from Pixel Bazaar. The logo files are attached to this project brief.

Key Sections to Include:
- Hero Section: An engaging introduction to Tollbrook Advisory with a strong visual impact.
- About Us: A brief overview of who we are and our mission.
- Team: Section for the profiles of the two principals.
- Services: A clear and concise presentation of our services, including franchise development, due diligence, and construction management.
- Contact Information: Easy-to-find contact details, including a form for inquiries.
- Call to Action: Encouraging visitors to get in touch with us for consultations or further information.

Design Considerations:
- Ensure the design is responsive and mobile-friendly.
- Include high-quality images and icons that complement our services and industry.
- We do not need development services, this is only a design project.

```html
<!DOCTYPE html>
<html lang="en">
<head>
<meta charset="utf-8">
<title>Tollbrook Advisory</title>
<link rel="stylesheet" href="https://fonts.googleapis.com/css2?family=Poppins:wght@400;500;600;700&display=swap">
<style>
:root{
  --ink:#1e2a32;
  --ink-soft:#2a3a44;
  --mint:#a9d6bf;
  --mint-pale:#cfe8da;
  --green:#6aae8c;
  --green-deep:#3f8a68;
  --text:#333d44;
  --muted:#6c757b;
  --white:#ffffff;
  --sky-top:#2f78c4;
  --sky-bottom:#9cc7e8;
}
*{box-sizing:border-box;margin:0;padding:0}
html,body{width:1200px;height:4808px;overflow:hidden}
body{font-family:"Poppins",sans-serif;color:var(--text);background:var(--white);position:relative;font-size:15px;line-height:1.6}
.abs{position:absolute}
.brand{display:flex;align-items:center;gap:12px;color:var(--white);font-weight:600;font-size:26px;line-height:1}
.brand-mark{width:34px;height:34px;border:3px solid var(--white);border-radius:6px}
.btn{display:inline-block;background:var(--green);color:var(--ink);font-weight:600;font-size:14px;padding:10px 20px;border-radius:3px;text-transform:uppercase}
.eyebrow{font-size:16px;color:var(--muted);text-align:center}
.section-title{font-size:40px;font-weight:600;color:var(--ink);text-align:center;line-height:1.2}

/* header */
.header{left:0;top:0;width:1200px;height:130px;z-index:3}
.header-logo-panel{left:0;top:0;width:430px;height:120px;background:var(--ink);border-bottom-right-radius:60px}
.header .brand{left:100px;top:30px}
.topbar{left:430px;top:0;width:770px;height:42px;background:var(--mint);display:flex;align-items:center;padding-left:20px;gap:30px;font-size:15px;color:var(--ink)}
.topbar span{display:flex;align-items:center;gap:8px}
.nav{left:440px;top:66px;display:flex;gap:36px;color:var(--white);font-size:16px;font-weight:500}
.socials{left:950px;top:60px;display:flex;gap:10px}
.socials i{width:30px;height:30px;border:2px solid var(--white);border-radius:50%;display:block}

/* hero */
.hero{left:0;top:0;width:1200px;height:800px}
.hero-photo{position:absolute;inset:0;background:linear-gradient(180deg,var(--sky-top) 0%,var(--sky-bottom) 55%,#6c8fa6 80%,#3e5566 100%)}
.hero-copy{left:100px;top:290px;color:var(--white);width:600px}
.hero-copy .kicker{font-size:17px;font-weight:500}
.hero-copy h1{font-size:42px;font-weight:700;line-height:1.2;margin-top:22px;text-transform:uppercase}
.hero-copy .tag{font-size:18px;font-weight:600;color:var(--mint-pale);margin-top:14px}
.hero-copy p{font-size:16px;margin-top:8px;max-width:480px}
.hero-copy .btn{margin-top:30px}
.hero-wave{left:0;top:600px}
.dots{left:568px;top:676px;display:flex;gap:8px}
.dots i{width:12px;height:12px;border-radius:50%;background:var(--ink);opacity:.5;display:block}
.dots i:first-child{opacity:1}

/* about */
.about-head{left:0;top:775px;width:1200px}
.about-intro{left:180px;top:880px;width:840px;text-align:center;font-size:15px;color:var(--muted)}
.about-photo{left:110px;top:1010px}
.about-copy{left:640px;top:1000px;width:500px;font-size:15px;color:var(--muted)}
.about-copy h3{font-size:27px;color:var(--ink);font-weight:600;margin:36px 0 8px}
.about-copy .btn{margin-top:28px}

/* services */
.services{left:0;top:1510px;width:1200px;height:1020px;background:var(--mint)}
.services-head{left:0;top:96px;width:1200px}
.services-head .eyebrow{color:var(--ink)}
.tabs{left:120px;top:190px;width:960px;display:flex;border:2px solid var(--ink)}
.tabs div{flex:1;font-size:14px;line-height:1.3;padding:8px 12px;color:var(--ink);font-weight:500;border-right:2px solid var(--ink)}
.tabs div:last-child{border-right:0}
.tabs .active{background:var(--ink);color:var(--white)}
.service-copy{left:120px;top:345px;width:480px;font-size:15px;color:var(--ink)}
.service-copy h3{font-size:28px;font-weight:600;font-style:italic}
.service-copy h4{font-size:16px;font-weight:600;margin:12px 0 14px}
.service-copy p{margin-bottom:12px}
.service-copy .btn{background:var(--ink);color:var(--white);margin-top:18px}
.service-photo{left:640px;top:250px}
.skyline{left:0;top:740px;width:1200px;height:280px;background:linear-gradient(180deg,var(--mint) 0%,#5d7b80 45%,var(--ink) 100%)}

/* team */
.team{left:0;top:2530px;width:1200px;height:560px;background:var(--ink)}
.team-head{left:0;top:0;width:1200px;color:var(--white)}
.team-head .eyebrow{color:#b7c3c9}
.team-head .section-title{color:var(--mint)}
.card{top:140px;width:470px;height:380px;background:var(--ink-soft);border-radius:12px;padding:28px 36px;text-align:center;color:#c9d2d6;font-size:14px}
.card.alt{border:2px solid var(--mint)}
.card-photo{width:130px;height:130px;border-radius:50%;margin:-62px auto 10px;background:linear-gradient(160deg,#d9dde0,#8b98a2);border:4px solid var(--white)}
.card h3{font-size:24px;color:var(--white);font-weight:600}
.card .role{font-size:15px;color:var(--white);margin-bottom:10px}
.card-contacts{display:flex;justify-content:center;gap:24px;margin-top:18px;font-size:12px}
.card-contacts span{display:flex;align-items:center;gap:6px}
.ico{width:24px;height:24px;border-radius:50%;background:var(--mint);display:inline-flex;align-items:center;justify-content:center}

/* contact */
.contact-head{left:0;top:3215px;width:1200px}
.contact-head .eyebrow{color:var(--green)}
.form{left:120px;top:3390px;width:460px}
.field{border:1px solid #c8cfd3;border-radius:3px;height:46px;font-size:13px;padding:12px;color:var(--text);margin-bottom:14px}
.row{display:flex;gap:12px}
.row .field{flex:1}
.field.tall{height:140px}
.form .btn{margin-top:6px;text-transform:none;padding:10px 26px}
.contact-diamond{left:590px;top:3220px}
.contact-list{left:760px;top:3382px;width:260px;color:var(--white);font-size:13px;line-height:1.4}
.contact-list li{list-style:none;display:flex;gap:14px;margin-bottom:22px}
.contact-list .ico{width:40px;height:40px;flex:none}
.contact-list b{display:block;font-size:17px;font-weight:500;margin-bottom:2px}
.map{left:100px;top:3870px;width:1000px;height:410px;background:linear-gradient(135deg,#eceeef,#d9dcde);border:1px solid #d0d4d6}

/* footer */
.footer{left:0;top:4360px;width:1200px;height:448px;background:var(--ink);color:var(--white);text-align:center}
.footer .brand{position:absolute;left:450px;top:140px;font-size:38px}
.footer .brand-mark{width:50px;height:50px}
.footer-nav{position:absolute;left:0;top:280px;width:1200px;display:flex;justify-content:center;gap:40px;font-size:17px}
.footer-social{position:absolute;left:0;top:336px;width:1200px;display:flex;justify-content:center;gap:12px}
.footer-social i{width:30px;height:30px;border-radius:50%;border:2px solid var(--white);display:block}
.footer-rule{position:absolute;left:100px;top:392px;width:1000px;border-top:1px solid #3f4d56}
.copyright{position:absolute;left:0;top:410px;width:1200px;font-size:14px}
</style>
</head>
<body>

<section class="abs hero">
  <div class="hero-photo" role="img" aria-label="Photo of a sunny Southern California city skyline by the water with a palm tree"></div>
  <svg class="abs hero-wave" width="1200" height="200" viewBox="0 0 1200 200"><path d="M0 90 C300 200 520 200 640 150 C800 80 1000 60 1200 120 L1200 200 L0 200 Z" fill="#ffffff"/></svg>
  <div class="abs dots"><i></i><i></i><i></i></div>
  <div class="abs hero-copy">
    <div class="kicker">Welcome To Tollbrook Advisory</div>
    <h1>Building Success<br>In Southern California</h1>
    <div class="tag">Expertise at Every Step: From Planning to Execution</div>
    <p>At Tollbrook, we blend innovative strategies with local market expertise to guide your commercial real estate ventures.</p>
    <span class="btn">Get In Touch</span>
  </div>
</section>

<header class="abs header">
  <div class="abs header-logo-panel"></div>
  <div class="abs brand"><span class="brand-mark"></span>Tollbrook Advisory</div>
  <div class="abs topbar">
    <span><svg width="18" height="14" viewBox="0 0 18 14"><rect x="1" y="1" width="16" height="12" rx="1" fill="none" stroke="#1e2a32" stroke-width="2"/><path d="M1 2l8 6 8-6" fill="none" stroke="#1e2a32" stroke-width="2"/></svg>info@tollbrookadvisory.example</span>
    <span><svg width="16" height="16" viewBox="0 0 24 24"><path d="M6 2l4 4-2 3c1 3 4 6 7 7l3-2 4 4-3 4C10 22 2 14 2 5z" fill="#1e2a32"/></svg>+1 555 014 2290</span>
  </div>
  <nav class="abs nav"><span>Home</span><span>About</span><span>Services</span><span>Team</span><span>Contact</span></nav>
  <div class="abs socials"><i></i><i></i><i></i><i></i></div>
</header>

<section>
  <div class="abs about-head">
    <div class="eyebrow">Welcome To Tollbrook Advisory</div>
    <h2 class="section-title">Tollbrook Advisory</h2>
  </div>
  <p class="abs about-intro">Welcome to Tollbrook Advisory, your trusted partner in navigating the complexities of the real estate and small business markets. Founded by industry veterans Rafael Dunmore and Owen Hale, we specialize in providing comprehensive services tailored to the unique needs of our clients.</p>
  <svg class="abs about-photo" width="400" height="460" viewBox="0 0 400 460" role="img" aria-label="Photo of business professionals meeting around a table">
    <defs><linearGradient id="aboutFill" x1="0" y1="0" x2="1" y2="1"><stop offset="0" stop-color="#e6e8ea"/><stop offset="1" stop-color="#8b949a"/></linearGradient></defs>
    <rect x="60" y="70" width="280" height="280" rx="60" transform="rotate(45 200 210)" fill="url(#aboutFill)" stroke="#a9d6bf" stroke-width="6"/>
  </svg>
  <div class="abs about-copy">
    <p>Whether you're a franchisee, a new restaurant owner, or a commercial real estate investor, our expertise in due diligence, construction management, and investment property evaluation ensures you make informed, strategic decisions.</p>
    <h3>Our Mission :</h3>
    <p>At Tollbrook Advisory, we are committed to your success. Our approach combines meticulous analysis, strategic insights, and personalized service to help you achieve your business goals. We pride ourselves on our ability to deliver results that exceed expectations, fostering long-term relationships built on trust and excellence.</p>
    <span class="btn">Learn More</span>
  </div>
</section>

<section class="abs services">
  <div class="abs services-head">
    <div class="eyebrow">What We Do</div>
    <h2 class="section-title">Tollbrook Services</h2>
  </div>
  <div class="abs tabs">
    <div class="active">Franchise Development &amp; Launch</div>
    <div>Due Diligence</div>
    <div>Building &amp; Construction Management</div>
    <div>Investment Property Evaluation</div>
    <div>Market Analysis &amp; Feasibility Studies</div>
  </div>
  <div class="abs service-copy">
    <h3>Franchise Development &amp; Launch</h3>
    <h4>Comprehensive franchise setup from evaluation to launch for scalable business growth.</h4>
    <p>At Tollbrook Advisory, our Franchise Development &amp; Launch service is designed to transform your successful business into a thriving franchise. We start by thoroughly evaluating your business model to determine its franchisability. Once confirmed, our team handles every aspect of the franchise setup, including legal documentation, branding, marketing strategies, operational guidelines, and franchisee recruitment.</p>
    <span class="btn">Learn More</span>
  </div>
  <svg class="abs service-photo" width="460" height="460" viewBox="0 0 460 460" role="img" aria-label="Photo of a hand touching a glowing network of business icons">
    <defs><radialGradient id="svcFill" cx=".5" cy=".45" r=".6"><stop offset="0" stop-color="#c98a4a"/><stop offset=".5" stop-color="#3b4a5a"/><stop offset="1" stop-color="#1a2530"/></radialGradient></defs>
    <rect x="80" y="80" width="300" height="300" rx="70" transform="rotate(45 230 230)" fill="url(#svcFill)"/>
  </svg>
  <div class="abs skyline" role="img" aria-label="Illustration of a dark city skyline silhouette with a bridge"></div>
</section>

<section class="abs team">
  <div class="abs team-head">
    <div class="eyebrow">Team</div>
    <h2 class="section-title">Our Leadership Team</h2>
  </div>
  <article class="abs card" style="left:110px">
    <div class="card-photo" role="img" aria-label="Portrait photo of Rafael Dunmore"></div>
    <h3>Rafael Dunmore</h3>
    <div class="role">Principal</div>
    <p>Rafael Dunmore brings almost 20 years of rich experience as a real estate investor and a pivotal role at one of Southern California's largest real estate management firms, where he honed his craft.</p>
    <div class="card-contacts">
      <span><i class="ico"><svg width="12" height="12" viewBox="0 0 24 24"><path d="M6 2l4 4-2 3c1 3 4 6 7 7l3-2 4 4-3 4C10 22 2 14 2 5z" fill="#1e2a32"/></svg></i>+1 555 014 2290</span>
      <span><i class="ico"><svg width="12" height="10" viewBox="0 0 18 14"><rect x="1" y="1" width="16" height="12" fill="none" stroke="#1e2a32" stroke-width="2"/><path d="M1 2l8 6 8-6" fill="none" stroke="#1e2a32" stroke-width="2"/></svg></i>info@rafaeldunmore.example</span>
    </div>
  </article>
  <article class="abs card alt" style="left:610px">
    <div class="card-photo" role="img" aria-label="Portrait photo of Owen Hale"></div>
    <h3>Owen Hale</h3>
    <div class="role">Principal</div>
    <p>Owen Hale is a seasoned real estate expert with extensive experience in project and construction management, and a licensed real estate agent in California, fluent in both English and Korean.</p>
    <div class="card-contacts">
      <span><i class="ico"><svg width="12" height="12" viewBox="0 0 24 24"><path d="M6 2l4 4-2 3c1 3 4 6 7 7l3-2 4 4-3 4C10 22 2 14 2 5z" fill="#1e2a32"/></svg></i>+1 555 014 2290</span>
      <span><i class="ico"><svg width="12" height="10" viewBox="0 0 18 14"><rect x="1" y="1" width="16" height="12" fill="none" stroke="#1e2a32" stroke-width="2"/><path d="M1 2l8 6 8-6" fill="none" stroke="#1e2a32" stroke-width="2"/></svg></i>info@owenhale.example</span>
    </div>
  </article>
</section>

<section>
  <div class="abs contact-head">
    <div class="eyebrow">Get In Touch</div>
    <h2 class="section-title">Contact Us</h2>
  </div>
  <form class="abs form">
    <div class="field">Name*</div>
    <div class="row"><div class="field">Email</div><div class="field">Phone</div></div>
    <div class="field">Company</div>
    <div class="field tall">Additional information</div>
    <span class="btn">Submit</span>
  </form>
  <svg class="abs contact-diamond" width="560" height="560" viewBox="0 0 560 560">
    <rect x="100" y="100" width="360" height="360" rx="70" transform="rotate(45 280 280)" fill="#1e2a32"/>
  </svg>
  <ul class="abs contact-list">
    <li><i class="ico"><svg width="16" height="20" viewBox="0 0 16 20"><path d="M8 0a7 7 0 0 0-7 7c0 5 7 13 7 13s7-8 7-13a7 7 0 0 0-7-7z" fill="#1e2a32"/><circle cx="8" cy="7" r="2.5" fill="#a9d6bf"/></svg></i><div><b>Location :</b>210 Meridian Way Suite 300,<br>Irvine, CA 92618, USA</div></li>
    <li><i class="ico"><svg width="16" height="16" viewBox="0 0 24 24"><path d="M6 2l4 4-2 3c1 3 4 6 7 7l3-2 4 4-3 4C10 22 2 14 2 5z" fill="#1e2a32"/></svg></i><div><b>Phone :</b>+1 555 014 2290</div></li>
    <li><i class="ico"><svg width="18" height="14" viewBox="0 0 18 14"><rect x="1" y="1" width="16" height="12" fill="none" stroke="#1e2a32" stroke-width="2"/><path d="M1 2l8 6 8-6" fill="none" stroke="#1e2a32" stroke-width="2"/></svg></i><div><b>Email :</b>info@tollbrook<br>advisory.example</div></li>
  </ul>
  <div class="abs map" role="img" aria-label="Street map of Irvine showing the office location pin"></div>
</section>

<footer class="abs footer">
  <div class="brand"><span class="brand-mark"></span>Tollbrook Advisory</div>
  <nav class="footer-nav"><span>Home</span><span>About</span><span>Services</span><span>Team</span><span>Contact</span></nav>
  <div class="footer-social"><i></i><i></i><i></i></div>
  <div class="footer-rule"></div>
  <div class="copyright">Copyright © 2024 Tollbrook Advisory</div>
</footer>

</body>
</html>
```